Velvet Lantern rebranding my business with a new business card

I have my new logo and now I need a refresher on my business cards. I really want something fun and fresh. I like black background or anything to make the color pop.
Logo
Name: Velvet Lantern
Contact Info as stated below:
Mira Pellow
555-013-4762
Logo
Name: Velvet Lantern
Mira Pellow
555-013-4762
fb.me/VelvetLanternbyMira
Instagram: @VelvetLanternbyMira

Industry/Entity Type

Business

Contact Information for Business Card

double-sided. Logo on one side. Contact info on the other.

Requirements
Must have
• Logo
• Name: Velvet Lantern
• Contact Info as stated below:
• Mira Pellow
• 555-013-4762
• fb.me/VelvetLanternbyMira
• fb.me/VelvetLanternbyMira

```html
<!DOCTYPE html>
<html lang="en">
<head>
<meta charset="utf-8">
<title>Velvet Lantern – Business Card</title>
<link href="https://fonts.googleapis.com/css2?family=Pinyon+Script&family=Didact+Gothic&display=swap" rel="stylesheet">
<style>
  :root {
    --canvas: #fbe3ee;
    --card-white: #ffffff;
    --card-pink: #e48ab5;
    --card-pink-soft: #eb9ab2;
    --ink-red: #d4464f;
    --mark-ink: #7a1f3f;
    --shadow: rgba(120, 40, 80, 0.22);
  }
  * { box-sizing: border-box; margin: 0; padding: 0; }
  html, body {
    width: 1200px; height: 1200px; overflow: hidden;
    background: var(--canvas);
  }
  .sheet {
    width: 1200px; height: 1200px;
    display: flex; flex-direction: column; align-items: center; justify-content: center;
    gap: 70px;
  }
  .card {
    position: relative;
    width: 840px; height: 480px;
    border-radius: 30px;
    overflow: hidden;
    box-shadow: 0 18px 40px var(--shadow);
  }
  /* Front */
  .card--front { background: var(--card-white); }
  .front-panel {
    position: absolute; inset: 0;
    width: 100%; height: 100%;
  }
  .logo-slot {
    position: absolute;
    display: flex; align-items: center; gap: 16px;
  }
  .logo-slot__dot {
    width: 34px; height: 34px; border-radius: 50%;
    background: var(--mark-ink);
    flex: none;
  }
  .logo-slot__name {
    font-family: "Didact Gothic", sans-serif;
    color: var(--mark-ink);
    font-size: 40px;
    white-space: nowrap;
  }
  .card--front .logo-slot { left: 60px; top: 300px; }
  .contact {
    position: absolute; right: 70px; top: 95px;
    text-align: center;
    color: var(--ink-red);
    font-family: "Didact Gothic", sans-serif;
  }
  .contact__business {
    font-family: "Pinyon Script", cursive;
    font-size: 68px; line-height: 1.1;
  }
  .contact__person { font-size: 38px; margin-top: 8px; }
  .contact__phone { font-size: 26px; margin-top: 14px; }
  .contact__web { font-size: 26px; margin-top: 12px; }
  /* Back */
  .card--back {
    background: linear-gradient(110deg, var(--card-pink) 0%, var(--card-pink-soft) 100%);
    display: flex; align-items: center; justify-content: center;
  }
  .card--back .logo-slot { position: static; }
</style>
</head>
<body>
<main class="sheet">
  <section class="card card--front" aria-label="Card front">
    <svg class="front-panel" viewBox="0 0 840 480" preserveAspectRatio="none" aria-hidden="true">
      <polygon points="0,170 330,170 520,480 0,480" fill="var(--card-pink)"/>
    </svg>
    <div class="logo-slot">
      <span class="logo-slot__dot"></span>
      <span class="logo-slot__name">Velvet Lantern</span>
    </div>
    <div class="contact">
      <p class="contact__business">Velvet Lantern</p>
      <p class="contact__person">Mira Pellow</p>
      <p class="contact__phone">555-013-4762</p>
      <p class="contact__web">fb.me/VelvetLanternbyMira</p>
    </div>
  </section>

  <section class="card card--back" aria-label="Card back">
    <div class="logo-slot">
      <span class="logo-slot__dot"></span>
      <span class="logo-slot__name">Velvet Lantern</span>
    </div>
  </section>
</main>
</body>
</html>
```